Logo and Card design for KRV Home Solutions LLC

I need an edgier logo and business card designs. Current logo attached. I like the colors below. I would like the logo to incorporate a home in the design.
Title = Principal-Acquisitions
Email:KRVHOMESOLUTIONS@fernmail.example
555-214-0937
facebook
IG
2 sided business card with the front being contact info a slogan about selling a home fast. The back incorporating What we do. Buy houses, land, or commercial property as is. We find solutions to make the process of selling simple and fair.

Target Market(s)

Motivated house sellers.

Industry/Entity Type

Business

Contact Information for Business Card

Who we are: We are a Faith based Real Estate Investment Company. We pay cash for homes in any condition and can close quick. Whatever the reason you need to sell fast, we can help. We believe in creating win-win solutions to help you in your time of need. We care! We can help!

Logo Text

KRV Home Solutions LLC

Font styles to use
Sans Serif

Colors
33a6d7
0355a3
85abd2
cee9f5
9d9d9d
b2b2b2
ffffff

Requirements
Must have
• Old logo attached. I want something edgier.
• Company name, phone number, description on the back of what we can do. Pay all cash. Buy in as is condition. No fees,Commisions or closing costs.Close quick. No hassles with solutions to meet your unique situation.
• Call today for an offer within 24 hours.

```html
<!DOCTYPE html>
<html lang="en">
<head>
<meta charset="utf-8">
<title>KRV Home Solutions – Business Card</title>
<link rel="stylesheet" href="https://fonts.googleapis.com/css2?family=Roboto:wght@400;500;700&family=Roboto+Condensed:wght@400;700&display=swap">
<style>
  :root {
    --navy: #1e3a70;
    --ink: #4a4a4a;
    --grey: #6b6b6b;
    --rule: #2a2a2a;
    --paper: #f3f5f7;
    --stage: #2c2c2c;
    --white: #ffffff;
  }
  * { margin: 0; padding: 0; box-sizing: border-box; }
  html, body { width: 1200px; height: 960px; overflow: hidden; }
  body {
    background: var(--stage);
    font-family: "Roboto", Arial, sans-serif;
    position: relative;
  }
  .card {
    position: absolute;
    width: 600px;
    height: 343px;
    overflow: hidden;
    box-shadow: 0 4px 10px rgba(0,0,0,.45);
  }
  /* ---------- Front ---------- */
  .card-front { left: 314px; top: 113px; background: var(--paper); }
  .front-photo {
    position: absolute; inset: 0 0 19px 0;
    background:
      radial-gradient(ellipse at 30% 75%, rgba(150,170,190,.35), transparent 55%),
      radial-gradient(ellipse at 80% 20%, rgba(170,195,175,.35), transparent 50%),
      linear-gradient(180deg, #eef2f5 0%, #e3e9ee 55%, #dfe7e4 100%);
  }
  .front-band {
    position: absolute; left: 0; right: 0; bottom: 0; height: 19px;
    background: var(--navy);
  }
  .brand-name {
    position: absolute; left: 38px; top: 96px;
    color: var(--navy); font-weight: 700; font-size: 24px; line-height: 28px;
  }
  .name-tab {
    position: absolute; right: 0; top: 151px; width: 18px; height: 40px;
    background: var(--navy);
  }
  .person {
    position: absolute; right: 34px; top: 149px; text-align: right;
  }
  .person-name {
    font-family: "Roboto Condensed", "Arial Narrow", sans-serif;
    font-size: 25px; font-weight: 700; color: var(--navy); line-height: 29px;
  }
  .person-title { font-size: 15px; font-weight: 400; color: var(--grey); line-height: 20px; }
  .divider {
    position: absolute; left: 37px; right: 35px; top: 200px; height: 1px;
    background: var(--rule);
  }
  .benefits {
    position: absolute; right: 34px; top: 220px; list-style: none; text-align: right;
    font-family: "Roboto Condensed", "Arial Narrow", sans-serif;
    font-size: 14.5px; line-height: 18px; color: var(--ink);
  }
  .benefits li { position: relative; padding-right: 14px; }
  .benefits li.bullet::after {
    content: ""; position: absolute; right: 0; top: 7px; width: 5px; height: 5px;
    border-radius: 50%; background: var(--navy);
  }
  .contacts {
    position: absolute; left: 31px; top: 257px; list-style: none;
    font-size: 14px; line-height: 19px; color: var(--ink);
  }
  .contacts li { display: flex; align-items: center; gap: 8px; }
  .contacts svg { width: 13px; height: 13px; flex: none; }
  /* ---------- Back ---------- */
  .card-back { left: 311px; top: 472px; background: var(--navy); color: var(--white); text-align: center; }
  .back-brand {
    position: absolute; left: 0; right: 0; top: 96px;
    font-size: 28px; font-weight: 700; line-height: 34px;
  }
  .back-copy { position: absolute; left: 0; right: 0; top: 156px; }
  .back-copy h2 { font-size: 15px; font-weight: 700; line-height: 20px; }
  .back-copy p { font-size: 15px; line-height: 18px; }
  .back-copy .what-we-do { margin-top: 17px; }
</style>
</head>
<body>
  <section class="card card-front" aria-label="Business card front">
    <div class="front-photo" role="img" aria-label="Faded photo of a house with a homeowner in front"></div>
    <div class="front-band"></div>

    <div class="brand-name">KRV Home Solutions LLC</div>

    <div class="name-tab"></div>
    <div class="person">
      <div class="person-name">EVAN MARLOW</div>
      <div class="person-title">Principal-Acquisitions</div>
    </div>
    <div class="divider"></div>

    <ul class="benefits">
      <li class="bullet">Pay all cash. Buy in as is condition</li>
      <li class="bullet">No fees,Commisions or closing costs</li>
      <li class="bullet">Close quick. No hassles with</li>
      <li>solutions to meet your unique situation</li>
      <li class="bullet">Call today for an offer within 24 hours</li>
    </ul>

    <ul class="contacts">
      <li>
        <svg viewBox="0 0 24 24" aria-hidden="true"><path fill="#1e3a70" d="M6.6 10.8a15.1 15.1 0 0 0 6.6 6.6l2.2-2.2c.3-.3.7-.4 1-.2 1.1.4 2.3.6 3.6.6.6 0 1 .4 1 1V20c0 .6-.4 1-1 1A17 17 0 0 1 3 4c0-.6.4-1 1-1h3.5c.6 0 1 .4 1 1 0 1.3.2 2.5.6 3.6.1.3 0 .7-.2 1z"/></svg>
        <span>555-214-0937</span>
      </li>
      <li>
        <svg viewBox="0 0 24 24" aria-hidden="true"><path fill="#1e3a70" d="M2 5h20v14H2z"/><path fill="none" stroke="#f3f5f7" stroke-width="2" d="M3 6l9 7 9-7"/></svg>
        <span>KRVHOMESOLUTIONS@fernmail.example</span>
      </li>
      <li>
        <svg viewBox="0 0 24 24" aria-hidden="true"><circle cx="12" cy="12" r="10" fill="#1e3a70"/><path fill="none" stroke="#f3f5f7" stroke-width="1.6" d="M2 12h20M12 2c3 3 3 17 0 20M12 2c-3 3-3 17 0 20"/></svg>
        <span>KRVHOMESOLUTIONS.example</span>
      </li>
    </ul>
  </section>

  <section class="card card-back" aria-label="Business card back">
    <div class="back-brand">KRV Home Solutions LLC</div>
    <div class="back-copy">
      <h2>WHO WE ARE</h2>
      <p>We are a Faith based Real Estate Investment Company. We pay cash for<br>
      homes in any condition and can close quick. Whatever the reason you need<br>
      to sell fast, we can help. We believe in creating win-win solutions to help</p>
      <h2 class="what-we-do">WHAT WE DO</h2>
      <p>Buy houses, land, or commercial property as is.<br>
      We find solutions to make the process of selling simple and fair.</p>
    </div>
  </section>
</body>
</html>
```